Road Construction Company needs business cards

We would like a new business card designed for our business.

We're a road construction company based in Qld, Australia.

Can the business card please have the following information on it.

Name: Warren Halbeck
Position: General Manager
Phone: 0472 915 348
Email: Warren.halbeck@tovrin.com.au
Address: 87 Marrow Ave, Pendlebay, QLD, 4023
Website: www.tovrin.com.au

Visually we'd like the card to be professional and simple.

Attached is our logo.

Our website is www.tovrin.com.au

Target Market(s)

Men aged 25-60

Contact Information for Business Card

As listed in project description

Font styles to use
Serif

Requirements
Must have
• Large logo on back of card

```html
<!DOCTYPE html>
<html lang="en">
<head>
<meta charset="utf-8">
<title>Tovrin Road Construction – Business Card</title>
<link href="https://fonts.googleapis.com/css2?family=Montserrat:wght@600;700;800&family=Poppins:wght@400;500&display=swap" rel="stylesheet">
<style>
  :root {
    --bg: #2c2e33;
    --navy: #1a4fa0;
    --royal: #0b56a8;
    --sky: #3aa3e0;
    --white: #ffffff;
    --ink: #4a4d52;
    --muted: #6a6e74;
  }
  * { box-sizing: border-box; margin: 0; padding: 0; }
  html, body { width: 1200px; height: 952px; overflow: hidden; }
  body {
    background: var(--bg);
    font-family: "Poppins", sans-serif;
    position: relative;
  }
  .card {
    position: absolute;
    left: 320px;
    width: 560px;
    height: 320px;
    overflow: hidden;
    box-shadow: 0 14px 30px rgba(0,0,0,.45);
  }
  .card--front { top: 100px; background: var(--white); }
  .card--back { top: 532px; background: var(--royal); }

  .brand {
    position: absolute;
    font-family: "Montserrat", sans-serif;
    font-weight: 800;
    letter-spacing: 1px;
    line-height: 1;
  }
  .card--front .brand { left: 44px; top: 78px; font-size: 46px; color: var(--navy); }
  .card--back .brand { left: 0; right: 0; top: 120px; text-align: center; font-size: 64px; color: var(--white); }

  .rule-thick { position: absolute; height: 5px; background: var(--sky); }
  .rule-thin { position: absolute; height: 1.5px; }
  .card--front .rule-thick { left: 0; top: 268px; width: 190px; }
  .card--front .rule-thin { left: 190px; right: 0; top: 271px; background: var(--navy); }
  .card--back .rule-thin { left: 0; width: 300px; top: 276px; background: var(--white); }
  .card--back .rule-thick { left: 300px; right: 0; top: 274px; }

  .contact-panel {
    position: absolute;
    left: 282px; top: 0; right: 0; height: 250px;
    background: linear-gradient(90deg, rgba(0,0,0,.07) 0, rgba(0,0,0,0) 30px);
    padding: 48px 0 0 34px;
  }
  .person-name {
    font-family: "Montserrat", sans-serif;
    font-weight: 700;
    font-size: 22px;
    color: var(--navy);
    letter-spacing: .5px;
  }
  .person-role { font-size: 12px; color: var(--muted); margin-top: 2px; }
  .role-underline { width: 70px; height: 1.5px; background: var(--navy); margin: 6px 0 14px; }
  .contact-list { list-style: none; }
  .contact-list li {
    display: flex; align-items: flex-start; gap: 9px;
    font-size: 11.5px; color: var(--ink); line-height: 1.35; margin-bottom: 7px;
  }
  .icon {
    flex: none; width: 17px; height: 17px; border-radius: 3px;
    background: var(--sky); display: flex; align-items: center; justify-content: center;
  }
</style>
</head>
<body>
  <section class="card card--front" aria-label="Business card front">
    <div class="brand">TOVRIN</div>
    <div class="rule-thick"></div>
    <div class="rule-thin"></div>
    <div class="contact-panel">
      <div class="person-name">WARREN HALBECK</div>
      <div class="person-role">General Manager</div>
      <div class="role-underline"></div>
      <ul class="contact-list">
        <li>
          <span class="icon"><svg width="11" height="11" viewBox="0 0 12 12"><path d="M6 1a3.5 3.5 0 0 0-3.5 3.5C2.5 7.3 6 11 6 11s3.5-3.7 3.5-6.5A3.5 3.5 0 0 0 6 1zm0 4.8a1.3 1.3 0 1 1 0-2.6 1.3 1.3 0 0 1 0 2.6z" fill="#fff"/></svg></span>
          <span>87 Marrow Ave, Pendlebay<br>QLD, 4023</span>
        </li>
        <li>
          <span class="icon"><svg width="11" height="11" viewBox="0 0 12 12"><path d="M3 1.5l1.6 2.3-.9 1.1c.6 1.3 1.6 2.3 2.9 2.9l1.1-.9 2.3 1.6-.8 1.8C5.6 10 2 6.4 1.7 2.3z" fill="#fff"/></svg></span>
          <span>0472 915 348</span>
        </li>
        <li>
          <span class="icon"><svg width="11" height="11" viewBox="0 0 12 12"><rect x="1.5" y="3" width="9" height="6" fill="none" stroke="#fff" stroke-width="1"/><path d="M1.5 3l4.5 3.5L10.5 3" fill="none" stroke="#fff" stroke-width="1"/></svg></span>
          <span>Warren.halbeck@tovrin.com.au</span>
        </li>
        <li>
          <span class="icon"><svg width="11" height="11" viewBox="0 0 12 12"><path d="M3 2l6 4-2.6.6L8 10l-1.2.6-1.6-3.4L3 9z" fill="#fff"/></svg></span>
          <span>www.tovrin.com.au</span>
        </li>
      </ul>
    </div>
  </section>

  <section class="card card--back" aria-label="Business card back">
    <div class="brand">TOVRIN</div>
    <div class="rule-thin"></div>
    <div class="rule-thick"></div>
  </section>
</body>
</html>
```